Climbing Gear Company Stationary Design

We need some new stationary to standardise our business.
We require:

Business Card
A4 Letterhead
With complements slip

Our business is a Distributor and retailer of rock climbing equipment throughout Australia.
We need to the stationary (business card in particular) to reflect this.

Target Market(s)

customers, other retail outlets, overseas manufacturers.

Industry/Entity Type

Business

Requirements
Must have
• company logo
website url- www.ridgetopgearworks.com.au
email - mark@ridgetopgearworks.com
Business Address: Unit 3, 14-16 Marlowe Street, Coffs Harbour, NSW, 2371
Phone: 0438 627 194
my Name (on Business card) - Gordon Pellimore
use of Blue colour in our logo

```html
<!DOCTYPE html>
<html lang="en">
<head>
<meta charset="utf-8">
<title>Ridgetop Gearworks – Business Card</title>
<link rel="stylesheet" href="https://fonts.googleapis.com/css2?family=Open+Sans:wght@400;600;700;800&display=swap">
<style>
  :root {
    --brand-blue: #2b3f8c;
    --shadow-lilac: #d9d9ee;
    --text-grey: #3a3a3a;
    --card-white: #ffffff;
    --backdrop: #ececec;
    --card-edge: #9a9a9a;
  }
  * { box-sizing: border-box; margin: 0; padding: 0; }
  html, body {
    width: 1200px; height: 1017px; overflow: hidden;
    background: var(--backdrop);
    font-family: "Open Sans", Arial, sans-serif;
  }
  .card {
    position: absolute;
    width: 737px; height: 421px;
    background: var(--card-white);
    border: 1px solid var(--card-edge);
    overflow: hidden;
  }
  .card--front { left: 82px; top: 53px; }
  .card--back { left: 350px; top: 528px; }

  .wordmark {
    color: var(--brand-blue);
    font-weight: 800;
    font-size: 44px;
    letter-spacing: 1px;
    line-height: 1;
    white-space: nowrap;
  }
  .tagline {
    color: var(--brand-blue);
    font-weight: 600;
    font-size: 18px;
    letter-spacing: 5px;
    line-height: 1;
    white-space: nowrap;
  }
  .card--front .wordmark { position: absolute; left: 33px; top: 62px; }
  .card--front .tagline { position: absolute; left: 35px; top: 122px; }

  .address {
    position: absolute; left: 31px; top: 208px;
    font-size: 17.5px; color: var(--text-grey);
  }
  .contact-list {
    position: absolute; left: 31px; top: 287px;
    list-style: none;
  }
  .contact-list li {
    display: flex; align-items: center; gap: 7px;
    font-size: 17.5px; color: var(--text-grey);
    height: 29.5px;
  }
  .contact-list svg { width: 13px; height: 13px; fill: var(--text-grey); flex: none; }

  .name-tab {
    position: absolute; left: 447px; top: 284px;
    width: 300px; height: 70px;
    background: var(--brand-blue);
    border-radius: 35px 0 0 35px;
    color: #fff; font-weight: 700; font-size: 23px;
    display: flex; align-items: center; padding-left: 33px;
  }
  .name-tab-shadow {
    position: absolute; left: 455px; top: 294px;
    width: 300px; height: 70px;
    background: var(--shadow-lilac);
    border-radius: 35px 0 0 35px;
  }

  .back-lockup {
    position: absolute; left: 0; right: 0; top: 172px;
    display: flex; flex-direction: column; align-items: center; gap: 16px;
  }
  .back-url {
    position: absolute; left: 0; right: 0; top: 358px;
    text-align: center;
    font-size: 17px; letter-spacing: 4.3px; color: var(--text-grey);
  }
</style>
</head>
<body>
  <section class="card card--front" aria-label="Business card front">
    <div class="wordmark">RIDGETOP GEARWORKS</div>
    <div class="tagline">THE ROPES•THE ROCK•THE OUTDOORS</div>

    <p class="address">Unit 3, 14-16 Marlowe Street, Coffs Harbour, NSW, 2371</p>

    <ul class="contact-list">
      <li>
        <svg viewBox="0 0 16 16" aria-hidden="true"><circle cx="8" cy="8" r="7.2" fill="none" stroke="#3a3a3a" stroke-width="1.3"/><path d="M5 4.5c.6-.5 1.2-.3 1.5.3l.6 1.3c.2.4 0 .8-.3 1l-.5.4c.4 1 1.2 1.8 2.2 2.2l.4-.5c.2-.3.6-.5 1-.3l1.3.6c.6.3.8.9.3 1.5-.8.9-2 1-3.3.3C6.6 10.4 5.6 9.4 4.9 7.8 4.3 6.5 4.2 5.3 5 4.5z"/></svg>
        0438 627 194
      </li>
      <li>
        <svg viewBox="0 0 16 16" aria-hidden="true"><path d="M1 4h14v9H1z"/><path d="M1 4l7 5 7-5" fill="none" stroke="#fff" stroke-width="1.2"/></svg>
        mark@ridgetopgearworks.com
      </li>
      <li>
        <svg viewBox="0 0 16 16" aria-hidden="true"><g fill="none" stroke="#3a3a3a" stroke-width="1.2"><circle cx="8" cy="8" r="6.5"/><ellipse cx="8" cy="8" rx="3" ry="6.5"/><path d="M1.5 8h13M2.7 4.5h10.6M2.7 11.5h10.6"/></g></svg>
        www.ridgetopgearworks.com.au
      </li>
    </ul>

    <div class="name-tab-shadow" aria-hidden="true"></div>
    <div class="name-tab">Gordon Pellimore</div>
  </section>

  <section class="card card--back" aria-label="Business card back">
    <div class="back-lockup">
      <div class="wordmark">RIDGETOP GEARWORKS</div>
      <div class="tagline">THE ROPES•THE ROCK•THE OUTDOORS</div>
    </div>
    <p class="back-url">www.ridgetopgearworks.com.au</p>
  </section>
</body>
</html>
```